Electric mountain bike tours nz

We are an Electric Mountain bike tour company in New Zealand. We will be offering bike rental and guided tours around the Nelson region in New Zealand. I want our website to represent both Mountain biking and New Zealand with the colours layout and features. We want tabs for the following:
-1 about us
-2 what we offer
-3 bookings/contact
Under the about us tab will be who we are as a a company. I want the ability to add videos to each of these tabs as we move foward with videos of the tracks we will be riding. I want the website to be editable so I can add and remove videos/photos myself. Also "our bikes" will be under this tab.
Under the what we offer tab will be
-1 bike rental and pricing
-2 guided tours and pricing
-3 recommended package deals.
I want to able to put the tracks under the guided tours tab and select beginner/ intermediate/advanced and have the tracks in each of the following to match the rider level. Also to be able to have a small video of the track would be great in this section.
Bookings and contact tab
(Further information for this tab to be updated soon)
Coded - Design and coding required
1 page
- Silver ferns, kiwi, mountains

```html
<!DOCTYPE html>
<html lang="en">
<head>
<meta charset="utf-8">
<title>Kowhai Trails – Electric Mountain Bike Tours</title>
<link href="https://fonts.googleapis.com/css2?family=Lato:wght@400;700;900&display=swap" rel="stylesheet">
<style>
:root{
  --navy:#142f56;
  --navy-dark:#0f2444;
  --ink:#2b2b2b;
  --grey:#8a8a8a;
  --light:#f4f4f4;
  --green:#2e8a72;
  --teal:#2aa3b3;
  --blue-service:#1d3c66;
  --footer:#1f2023;
  --white:#ffffff;
  --nav-active:#6f8fd6;
}
*{box-sizing:border-box;margin:0;padding:0}
html,body{width:1200px;height:3396px;overflow:hidden}
body{position:relative;font-family:'Lato',sans-serif;color:var(--ink);background:var(--white)}
.abs{position:absolute}
.center{text-align:center}

/* Header */
.hero-photo{left:0;top:0;width:1200px;height:740px;
  background:radial-gradient(ellipse at 55% 35%,#4b6a2e 0%,#2d4419 35%,#141a10 75%,#0b0d0a 100%)}
.header-bar{left:0;top:0;width:1200px;height:124px;background:linear-gradient(#000 0%,rgba(0,0,0,.85) 60%,rgba(0,0,0,0))}
.brand{left:102px;top:-34px;width:204px;height:204px;border-radius:50%;background:#000;display:flex;align-items:center;justify-content:center;padding-top:30px}
.brand span{color:var(--white);font-weight:900;font-size:22px;letter-spacing:1px;text-align:center;line-height:1.1}
.nav{top:55px;left:0;width:1200px;font-size:13px;font-weight:400;color:var(--white);letter-spacing:.5px}
.nav a{position:absolute;color:inherit;text-decoration:none;white-space:nowrap}
.nav a.active{color:var(--nav-active)}
.nav a.active::after{content:"";position:absolute;left:-6px;right:-6px;top:53px;height:3px;background:var(--nav-active)}
.hero-title{top:332px;width:1200px;font-size:37px;font-weight:900;color:var(--white);letter-spacing:2px}
.hero-sub{top:384px;width:1200px;font-size:19px;color:var(--white)}
.slider-arrow{top:345px}

/* Welcome */
.welcome{left:0;top:668px;width:1200px;height:444px;background:var(--navy);clip-path:polygon(0 68px,100% 0,100% 100%,0 100%)}
.welcome h2{position:absolute;top:120px;width:1200px;text-align:center;color:var(--white);font-size:32px;font-weight:700}
.rule{position:absolute;height:3px;width:80px;left:560px}
.welcome .rule{top:167px;background:var(--white)}
.welcome p{position:absolute;top:190px;left:168px;width:864px;text-align:center;color:var(--white);font-size:19px;line-height:26px}
.btn-outline{position:absolute;left:503px;top:310px;width:194px;height:50px;border:2px solid var(--white);color:var(--white);font-weight:700;font-size:19px;display:flex;align-items:center;justify-content:center}

/* Section headings */
.section-title{width:1200px;text-align:center;font-size:34px;font-weight:700;color:var(--ink)}
.section-rule{left:560px;width:80px;height:3px;background:var(--ink)}

/* Services */
.services{left:0;top:1112px;width:1200px;height:523px;background:var(--white)}
.service{top:1290px;width:300px;text-align:center}
.service-badge{width:150px;height:150px;margin:0 auto;border-radius:50%;background:currentColor;opacity:.85}
.service h3{margin-top:22px;font-size:16px;font-weight:900}
.service p{margin-top:10px;font-size:13px;line-height:19px;color:var(--grey);padding:0 36px}

/* Video */
.video{left:0;top:1635px;width:1200px;height:432px;background:linear-gradient(180deg,#6f7680 0%,#8a8f96 40%,#3f4245 70%,#2a2b2d 100%)}
.video-title{top:1722px;width:1200px;text-align:center;color:var(--white);font-size:32px;font-weight:700}

/* Blog */
.blog{left:0;top:2067px;width:1200px;height:593px;background:var(--light)}
.post{top:2235px;width:299px;height:228px;color:var(--white);box-shadow:0 4px 10px rgba(0,0,0,.25);border:4px solid var(--white)}
.post h4{position:absolute;left:14px;right:14px;font-size:16px;font-weight:900;line-height:19px}
.post .date{position:absolute;left:14px;font-size:10px;font-weight:700}
.post .more{position:absolute;left:14px;font-size:11px;font-weight:900}
.btn-solid{left:525px;top:2540px;width:150px;height:41px;background:var(--navy-dark);color:var(--white);font-weight:700;font-size:16px;display:flex;align-items:center;justify-content:center}

/* Clients */
.client{top:2823px;width:181px;height:120px;border:2px solid #e6e6e6;background:var(--white);display:flex;align-items:center;justify-content:center;font-size:16px;font-weight:700;color:#222;text-align:center}

/* Footer */
.footer{left:0;top:3018px;width:1200px;height:378px;background:var(--footer);color:#c9c9c9}
.footer-mark{left:102px;top:82px;width:204px;height:204px;border-radius:50%;border:6px solid #36383c;display:flex;align-items:center;justify-content:center;color:#3b3d41;font-weight:900;font-size:24px}
.footer h5{position:absolute;top:74px;font-size:18px;font-weight:700;color:var(--white)}
.footer ul{position:absolute;top:112px;list-style:none;font-size:12px;line-height:32px}
.footer-line{left:441px;top:304px;width:700px;height:1px;background:#3a3b3f}
.copyright{top:332px;width:1200px;text-align:center;font-size:11px;color:#bdbdbd}
.copy-code{right:40px;top:332px;font-size:11px}
.socials{left:955px;top:236px;display:flex;gap:8px}
.socials span{width:16px;height:16px;border-radius:50%;background:#c9c9c9}
</style>
</head>
<body>

<div class="abs hero-photo" role="img" aria-label="Electric mountain bike in front of a lush silver fern backdrop"></div>
<div class="abs header-bar"></div>
<div class="abs brand"><span>KOWHAI<br>TRAILS</span></div>
<nav class="abs nav">
  <a class="active" style="left:532px">HOME</a>
  <a style="left:626px">ABOUT US</a>
  <a style="left:740px">WHAT WE OFFER</a>
  <a style="left:900px">BOOKINGS</a>
  <a style="left:1018px">CONTACT US</a>
</nav>
<h1 class="abs hero-title center">ELECTRIC MOUNTAIN BIKE TOURS IN NEW ZEALAND</h1>
<p class="abs hero-sub center">We will be offering bike rental and guided tours around the Nelson region in New Zealand.</p>
<svg class="abs slider-arrow" style="left:32px" width="18" height="30" viewBox="0 0 18 30"><path d="M15 2 3 15l12 13" fill="none" stroke="#ffffff" stroke-opacity=".7" stroke-width="2"/></svg>
<svg class="abs slider-arrow" style="left:1150px" width="18" height="30" viewBox="0 0 18 30"><path d="M3 2l12 13L3 28" fill="none" stroke="#ffffff" stroke-opacity=".7" stroke-width="2"/></svg>

<section class="abs welcome">
  <h2>WELCOME TO KOWHAI TRAILS</h2>
  <div class="rule"></div>
  <p>Lorem ipsum dolor sit amet, consectetur adipiscing elit, sed do eiusmod tempor incididunt ut labore et dolore magna aliqua. Ut enim ad minim veniam, quis nostrud exercitation ullamco laboris nisi ut aliquip ex ea commodo consequat.</p>
  <div class="btn-outline">CONTACT US</div>
</section>

<section class="abs services"></section>
<h2 class="abs section-title" style="top:1186px">OUR SERVICES</h2>
<div class="abs section-rule" style="top:1238px"></div>

<div class="abs service" style="left:81px;color:var(--green)">
  <div class="service-badge" role="img" aria-label="Numbered gear badge with a rental bike illustration"></div>
  <h3>BIKE RENTAL AND PRICING</h3>
  <p>Sed ut perspiciatis unde omnis iste natus error sit voluptatem accusantium doloremque laudantium.</p>
</div>
<div class="abs service" style="left:454px;color:var(--teal)">
  <div class="service-badge" role="img" aria-label="Numbered gear badge with a guided trail illustration"></div>
  <h3>GUIDED TOURS AND PRICING</h3>
  <p>Sed ut perspiciatis unde omnis iste natus error sit voluptatem accusantium doloremque laudantium.</p>
</div>
<div class="abs service" style="left:817px;color:var(--blue-service)">
  <div class="service-badge" role="img" aria-label="Numbered gear badge with a package deal illustration"></div>
  <h3>RECOMMENDED PACKAGE DEALS</h3>
  <p>Sed ut perspiciatis unde omnis iste natus error sit voluptatem accusantium doloremque laudantium.</p>
</div>

<section class="abs video" role="img" aria-label="Cyclist riding along an open road through mountain country"></section>
<h2 class="abs video-title">OUR VIDEO</h2>
<svg class="abs" style="left:548px;top:1800px" width="104" height="104" viewBox="0 0 104 104"><circle cx="52" cy="52" r="50" fill="#fff"/><path d="M43 36l24 16-24 16z" fill="#111"/></svg>

<section class="abs blog"></section>
<h2 class="abs section-title" style="top:2122px">OUR BLOG</h2>
<div class="abs section-rule" style="top:2171px"></div>

<article class="abs post" style="left:104px;background:linear-gradient(135deg,#5a7a1e,#3b5512 60%,#24340c)" role="img" aria-label="Close-up of sliced kiwifruit">
  <h4 style="top:130px">CONSEQUUNTUR MAGNI DOLORES EOS QUI RATIONE</h4>
  <span class="date" style="top:178px">APRIL 14, 2015</span>
</article>
<article class="abs post" style="left:450px;background:linear-gradient(180deg,#2c3a4f,#4d5f72 55%,#8a7b66)" role="img" aria-label="Mountain bikers on a coastal trail at dusk">
  <h4 style="top:70px">NUMQUAM EIUS MODI TEMPORA INCIDUNT</h4>
  <span class="date" style="top:124px">JANUARY 20, 2015</span>
  <span class="more" style="top:154px">READ MORE &#10140;</span>
</article>
<article class="abs post" style="left:797px;background:linear-gradient(135deg,#2f4a24,#4f6c34 50%,#1d2c15)" role="img" aria-label="Rider on a forest track among ferns">
  <h4 style="top:130px">EXERCITATIONEM ULLAM CORPORIS SUSCIPIT</h4>
  <span class="date" style="top:178px">APRIL 14, 2015</span>
</article>
<div class="abs btn-solid">VIEW MORE</div>

<h2 class="abs section-title" style="top:2715px">OUR CLIENTS</h2>
<div class="abs section-rule" style="top:2765px"></div>
<svg class="abs" style="left:78px;top:2870px" width="16" height="28" viewBox="0 0 16 28"><path d="M14 2 3 14l11 12" fill="none" stroke="#cfcfcf" stroke-width="2"/></svg>
<svg class="abs" style="left:1104px;top:2870px" width="16" height="28" viewBox="0 0 16 28"><path d="M2 2l11 12L2 26" fill="none" stroke="#cfcfcf" stroke-width="2"/></svg>
<div class="abs client" style="left:115px">Ridgeway Cycles</div>
<div class="abs client" style="left:312px">Tasman Wheel</div>
<div class="abs client" style="left:509px">Fernline</div>
<div class="abs client" style="left:706px">Kea Loop Tours</div>
<div class="abs client" style="left:903px">Summit Spoke</div>

<footer class="abs footer">
  <div class="abs footer-mark">KOWHAI</div>
  <h5 style="left:441px">Quick Links</h5>
  <ul style="left:443px"><li>Home</li><li>About Us</li><li>What We Offer</li><li>Bookings</li><li>Contact Us</li></ul>
  <h5 style="left:672px">Hours</h5>
  <ul style="left:674px"><li>Monday - Friday: 10:00 - 17:00</li><li>Saturday: 10:00 - 14:00</li><li>Sunday: Holiday</li></ul>
  <h5 style="left:955px">Contact Us</h5>
  <ul style="left:957px;line-height:24px">
    <li><svg width="9" height="12" viewBox="0 0 9 12"><path d="M4.5 0A4.5 4.5 0 0 0 0 4.5C0 8 4.5 12 4.5 12S9 8 9 4.5A4.5 4.5 0 0 0 4.5 0z" fill="#c9c9c9"/></svg> KOWHAI TRAILS<br>&nbsp;&nbsp;&nbsp;New Zealand</li>
    <li><svg width="10" height="10" viewBox="0 0 10 10"><path d="M2 0l2 3-1 1.5a6 6 0 0 0 2.5 2.5L7 6l3 2-1 2C4 10 0 6 0 1z" fill="#c9c9c9"/></svg> 021 555 0147</li>
    <li><svg width="11" height="8" viewBox="0 0 11 8"><rect width="11" height="8" fill="#c9c9c9"/><path d="M0 0l5.5 4L11 0" fill="none" stroke="#1f2023"/></svg> hello@kowhaitrails.nz</li>
  </ul>
  <div class="abs socials" aria-label="Social media links"><span></span><span></span><span></span><span></span><span></span></div>
  <div class="abs footer-line"></div>
  <p class="abs copyright">© 2018 KOWHAI TRAILS . All right reserved . Term of Use</p>
  <span class="abs copy-code">C16</span>
</footer>

</body>
</html>
```